Alaska Law Firm Needs a Sticker Design

We need a design for stickers to put on already-printed brochures. We mail the brochures to potential clients so they can learn more about accident-induced injuries, insurance claims, legal representation, and our own law firm.

One of our lawyers wrote a book that provides a helpful overview of personal injury claims. We are offering this book for free to anyone who calls and requests it. Therefore, the sticker design should include one of the following phrases, or something very similar:
a) "Still have questions? Call and request our book-- for free!"
b) "Still have questions about auto accident claims? Call and request our book today."
c) "Still have questions about filing a claim? Call and request a free copy of our book."
d) "Still have questions? Call us today to request a free copy of our book, Clear Lanes Ahead."
e) "To learn more about automobile accidents and insurance, call today and request a free copy of our book."

The sticker should be approximately 3"x3" and may be a circle, square, rectangle, or ellipsis. The sticker will be placed on the back of the folder, which is light blue. We would like the sticker to match the color scheme of our website and the folder.

I will upload an image of the book cover as soon as I obtain it.

Law Firm

Font styles to use
Serif
Sans Serif

Requirements
Should not have
• Bright colors that aren't already used in the folder design. e.g. no bright orange, pink, chartreuse, turquoise, yellow, red.

```html
<!DOCTYPE html>
<html lang="en">
<head>
<meta charset="utf-8">
<title>Book Offer Sticker</title>
<link rel="stylesheet" href="https://fonts.googleapis.com/css2?family=Cinzel:wght@400;500&family=Montserrat:wght@400;800&family=Open+Sans:wght@400;600&display=swap">
<style>
  :root {
    --sky: #d8e6f7;
    --navy: #173f68;
    --ink: #141b48;
    --paper: #ffffff;
    --accent-red: #c0282d;
    --text-grey: #333a45;
    --lawn: #6d9a4a;
    --lawn-light: #b8cfa3;
  }
  html, body { margin: 0; padding: 0; overflow: hidden; background: #ffffff; }
  .canvas { position: relative; width: 1200px; height: 1200px; overflow: hidden; background: #ffffff; }

  .sticker {
    position: absolute; left: 43px; top: 67px; width: 1114px; height: 1114px;
    border-radius: 50%; background: var(--sky); overflow: hidden;
    box-shadow: 0 0 0 1px var(--navy);
  }
  .headline, .offer, .free-line {
    position: absolute; left: 0; width: 1200px; margin: 0; text-align: center;
    font-family: 'Cinzel', serif; font-weight: 400;
  }
  .headline-top { top: 82px; font-size: 96px; color: var(--navy); line-height: 1; }
  .headline-main { top: 183px; font-size: 124px; color: var(--navy); line-height: 1; letter-spacing: 2px; }

  .offer-band { position: absolute; left: -43px; top: 321px; width: 1200px; height: 216px; background: var(--navy); }
  .offer { color: var(--sky); font-size: 66px; line-height: 1; }
  .offer-call { top: 356px; }
  .offer-request { top: 460px; }
  .free-line { top: 560px; font-size: 84px; color: var(--navy); letter-spacing: 4px; line-height: 1; }
  .headline, .offer, .free-line { margin-left: -43px; }

  .book {
    position: absolute; left: 377px; top: 737px; width: 467px; height: 360px;
    background: var(--ink); border: 1px solid #000; box-sizing: border-box;
  }
  .back-cover {
    position: absolute; left: 3px; top: 3px; width: 228px; height: 315px; background: var(--paper);
    font-family: 'Open Sans', sans-serif; color: var(--text-grey); font-size: 5.2px; line-height: 1.3;
    padding: 12px 12px 0; box-sizing: border-box;
  }
  .back-lead { color: var(--accent-red); font-weight: 600; text-align: center; margin: 0 0 5px; font-size: 5.4px; }
  .back-cover p { margin: 0 0 5px; text-align: justify; }
  .back-rule { height: 1px; background: var(--accent-red); margin: 6px 30px 8px; }
  .author-row { display: flex; gap: 6px; }
  .author-photo { flex: 0 0 56px; height: 72px; background: linear-gradient(#c9d3df, #3550a0); }
  .firm-name {
    position: absolute; left: 12px; bottom: 10px; display: flex; align-items: center; gap: 5px;
    font-family: 'Cinzel', serif; font-size: 11px; color: var(--ink); line-height: 1.05;
  }
  .firm-square { width: 18px; height: 18px; background: var(--ink); }

  .spine {
    position: absolute; left: 233px; top: 3px; width: 5px; height: 315px;
  }
  .spine-text {
    position: absolute; left: 240px; top: 110px; transform-origin: 0 0; transform: rotate(90deg);
    font-family: 'Open Sans', sans-serif; font-size: 5px; color: var(--paper); white-space: nowrap; letter-spacing: .3px;
  }
  .front-cover {
    position: absolute; left: 238px; top: 3px; width: 225px; height: 315px; background: var(--paper);
    text-align: center; overflow: hidden;
  }
  .front-author { margin: 14px 0 4px; font-family: 'Montserrat', sans-serif; font-size: 12px; color: var(--ink); letter-spacing: -.3px; }
  .front-title { margin: 0; font-family: 'Montserrat', sans-serif; font-weight: 800; font-size: 27px; line-height: .95; color: var(--ink); letter-spacing: -.5px; }
  .front-photo {
    position: absolute; left: 0; top: 92px; width: 225px; height: 223px;
    background: linear-gradient(180deg, #e9eef2 0%, var(--lawn-light) 35%, var(--lawn) 100%);
  }
  .book-strap {
    position: absolute; left: 238px; top: 320px; width: 225px;
    font-family: 'Open Sans', sans-serif; font-weight: 600; font-size: 10.5px; line-height: 1.3;
    color: var(--paper); text-align: center;
  }
</style>
</head>
<body>
<div class="canvas">
  <div class="sticker">
    <h1 class="headline headline-top">Still have</h1>
    <h1 class="headline headline-main">QUESTIONS?</h1>
    <div class="offer-band"></div>
    <p class="offer offer-call">CALL (907) 555-0142</p>
    <p class="offer offer-request">AND REQUEST OUR BOOK</p>
    <p class="free-line">FOR FREE</p>
  </div>

  <div class="book">
    <div class="back-cover">
      <p class="back-lead">MOST OF US WILL BE IN AN AUTO ACCIDENT AT LEAST ONCE. INSURERS PUT THE NUMBER CLOSER TO THREE OR FOUR.</p>
      <p>If you have never been in a car accident, consider yourself lucky. It is always best to be prepared.</p>
      <p>If you were recently in a crash and are unsure what to expect, this book explains your rights and the steps to take next.</p>
      <div class="back-rule"></div>
      <div class="author-row">
        <div class="author-photo" role="img" aria-label="Author portrait photograph"></div>
        <div>
          <p>Daniel studied biology at university before law school, then spent years learning how insurers handle injury claims.</p>
          <p>He now helps injured people across Alaska receive full and fair compensation.</p>
        </div>
      </div>
      <p style="margin-top:6px">Most cases settle out of court, but insurers pay fairly when they see the threat of trial is real.</p>
      <div class="firm-name"><span class="firm-square"></span><span>Whitcomb<br>Law Group</span></div>
    </div>
    <div class="spine"></div>
    <div class="spine-text">CLEAR LANES AHEAD &nbsp;&nbsp;&nbsp;&nbsp; DANIEL R. WHITCOMB</div>
    <div class="front-cover">
      <p class="front-author">DANIEL R. WHITCOMB</p>
      <h2 class="front-title">CLEAR LANES<br>AHEAD</h2>
      <div class="front-photo" role="img" aria-label="Photo of a smiling family lying on a lawn beside a small red car"></div>
    </div>
    <div class="book-strap">THE RIGHT WAY TO HANDLE<br>YOUR AUTO ACCIDENT CLAIM</div>
  </div>
</div>
</body>
</html>
```